Harlow Denatl Laboratory nees a window design

We want to make a window cover 8 feet wide and 6 feet tall to advertise our dental lab with all the products we produce<br/>: Digital Cad/Cam<br/>: Implants<br/>: Dentures<br/>: Cast Partials <br/>: Orthodontic appliances<br/><br/> and it has to include a service we provide for a denturist on site by appointment only.<br/><br/>Please use the sample logo below our colours are white backround and blue letters

Font styles to use
Script

Colors
ffffff
0355a3

Requirements
Nice to have
• a picture of a teddy bear on a dental chair, or some dental work particularly bridge work since our moto is Building bridges since 1976
Should not have
• real people

```html
<!DOCTYPE html>
<html lang="en">
<head>
<meta charset="utf-8">
<title>Harlow Dental Laboratory – Window Cover</title>
<link rel="stylesheet" href="https://fonts.googleapis.com/css2?family=Great+Vibes&family=Source+Sans+3:wght@600&display=swap">
<style>
  :root {
    --page-bg: #ffffff;
    --brand-blue: #0355a3;
    --panel-deep: #0355a3;
    --panel-mid: #1b8fd0;
    --panel-bright: #10e6ee;
    --panel-pale: #b4f6f4;
    --text-white: #ffffff;
    --accent-pink: #e8336b;
    --mascot-blue: #4aa6ea;
    --mascot-light: #9fd4f7;
    --tooth-white: #f4f6f7;
    --tooth-shade: #cfd5d8;
    --chair-light: #7fe3ef;
  }
  * { box-sizing: border-box; margin: 0; padding: 0; }
  html, body {
    width: 1200px; height: 1200px; overflow: hidden;
    background: var(--page-bg);
  }
  .window-cover {
    position: absolute; left: 40px; top: 108px;
    width: 1120px; height: 984px; overflow: hidden;
    background:
      radial-gradient(ellipse 70% 80% at 80% 35%, var(--panel-pale) 0%, var(--panel-bright) 30%, transparent 65%),
      linear-gradient(100deg, var(--panel-deep) 0%, var(--panel-mid) 45%, var(--panel-bright) 75%);
    font-family: "Source Sans 3", "Myriad Pro", sans-serif;
    font-weight: 600;
    color: var(--text-white);
  }
  .brand-name {
    position: absolute; left: 0; right: 0; top: 60px;
    text-align: center; font-weight: 600;
    font-size: 66px; line-height: 1; letter-spacing: 1px;
  }
  .brand-name .brand-sub {
    display: block; font-size: 34px; margin-top: 10px; letter-spacing: 2px;
  }
  .product-list { position: absolute; left: 0; top: 0; list-style: none; }
  .product-item {
    position: absolute; left: 0; height: 50px;
    display: flex; align-items: center;
    font-size: 44px; white-space: nowrap;
  }
  .product-item .marker-line {
    width: 38px; height: 8px; background: var(--accent-pink);
  }
  .product-item .marker-dot {
    width: 34px; height: 34px; border-radius: 50%;
    background: var(--text-white); border: 7px solid var(--accent-pink);
    margin-left: -4px; margin-right: 28px;
  }
  .item-cadcam { top: 250px; }
  .item-implants { top: 330px; }
  .item-dentures { top: 410px; }
  .item-partials { top: 490px; }
  .item-ortho { top: 570px; }
  .denturist-note {
    position: absolute; left: 40px; top: 655px; width: 570px;
    font-family: "Great Vibes", cursive; font-weight: 400;
    font-size: 44px; line-height: 1.15; color: var(--text-white);
  }
  .mascot-art {
    position: absolute; left: 634px; top: 168px; width: 486px; height: 760px;
    border-radius: 200px 200px 40px 40px;
    background: linear-gradient(180deg, var(--mascot-blue) 0%, var(--mascot-light) 100%);
  }
  .chair-art {
    position: absolute; left: 0; top: 790px; width: 340px; height: 194px;
    background: linear-gradient(160deg, transparent 10%, var(--chair-light) 60%, rgba(255,255,255,0.6) 100%);
  }
  .teeth-art { position: absolute; left: 0; top: 0; width: 1120px; height: 984px; }
</style>
</head>
<body>
  <main class="window-cover">
    <h1 class="brand-name">HARLOW<span class="brand-sub">Dental Laboratory</span></h1>

    <ul class="product-list">
      <li class="product-item item-cadcam"><span class="marker-line"></span><span class="marker-dot"></span>Digital Cad/Cam</li>
      <li class="product-item item-implants"><span class="marker-line"></span><span class="marker-dot"></span>Implants</li>
      <li class="product-item item-dentures"><span class="marker-line"></span><span class="marker-dot"></span>Dentures</li>
      <li class="product-item item-partials"><span class="marker-line"></span><span class="marker-dot"></span>Cast Partials</li>
      <li class="product-item item-ortho"><span class="marker-line"></span><span class="marker-dot"></span>Orthodontic Appliances</li>
    </ul>

    <p class="denturist-note">Denturist on site – by appointment only</p>

    <div class="chair-art" role="img" aria-label="Illustration of a dental chair with an overhead lamp"></div>
    <div class="mascot-art" role="img" aria-label="Illustration of a grinning blue bear mascot with crossed arms"></div>

    <svg class="teeth-art" viewBox="0 0 1120 984" role="img" aria-label="Illustration of a row of large white teeth on pink gum">
      <defs>
        <linearGradient id="toothFill" x1="0" y1="0" x2="0" y2="1">
          <stop offset="0" stop-color="#f4f6f7"/>
          <stop offset="1" stop-color="#cfd5d8"/>
        </linearGradient>
      </defs>
      <path d="M356 984 Q420 950 520 940 Q640 930 760 900 Q880 860 960 800 Q1040 760 1120 740 L1120 984 Z" fill="url(#toothFill)"/>
      <path d="M940 984 Q1040 930 1120 880 L1120 984 Z" fill="#e8336b"/>
    </svg>
  </main>
</body>
</html>
```